Hardcore nerd needs to stand out in a sea of dull Defence business cards

Wombarra Devices is a new Australian consulting engineering company that turns research and theory into practical systems. No evangelistic fluff, just mathematics and physics into electronic and optical circuits for consumer products, scientific research or Defence applications.

We already have a recognised logo (provided) which is often dark blue/black on a light background but we're open to other combinations. (Us engineers tend to have limited aesthetic imagination :)

Some of our recent products have included:
* Instrumentation for electrical testing,
* Radar jammers,
* GPS antenna design,
* Satellite tracking systems,
* High power lasers

We're open to both single and double-sided designs - happy to be convinced either way.

P.S. Another group is working on the web page, so - alas - our web site is currently of no use for images/ideas...

Target Market(s)

Engineering managers,
Scientists

Contact Information for Business Card

Dr Colin Harte
R&D Engineer

colin@wombarradevices.com.au
0427 563 710

PO Box XXX (to be confirmed)
Kelsby ACT 2917
Australia

Font styles to use
Serif
Sans Serif

Colors

Designer to choose colors to be used in the design.

Requirements
Must have
• My contact details!
• I've had many (great) "bold and plain" designs submitted already, so feel free to be artistically creative :)
• Happy to take advice re fonts/colours/printability etc.
Nice to have
• I'm not sure if "lists" are more at home on a CV than a business card, but representative services include:
• Applied electromagnetics
• RF and high speed electronics
• Signal and image processing
• Electro-optical and laser systems
• Concept-to-prototype design services
• If you're considering double sided cards, then often measuring/alignment grids/rulers feature on the back of similar cards.
• e.g. https://www.veltranoptics.example/newgrouppage9.cfm?objectgroup_id=4183
• https://www.veltranoptics.example/newgrouppage9.cfm?objectgroup_ID=4185
• ..or even a "Smith chart" (google will return lots)
• Generic images to represent a capability might work - googling images associated with keyword for each of these areas might help:
• - "passive radar", "phased array", "fdtd", "vircator"
• RF and high speed electronic design
• - "smith chart", "microstrip circuits", "dimensioned drawing", "electronic schematic"
• - "dft", "iir filter"
• - "optical cavity". "laser energy level diagram"
• Background/watermarked images outlines/wireframes/schematics would probably look OK.
Should not have
• If a list of projects/services is provided, it is important not to make the client feel that this is "all" the company can do. Engineering design is a creative discipline (like graphics :)
• Please, no stock "military" snaps like planes, missiles, etc!

```html
<!DOCTYPE html>
<html lang="en">
<head>
<meta charset="utf-8">
<title>Wombarra Devices – Business Card</title>
<link href="https://fonts.googleapis.com/css2?family=Lato:wght@300;400;700;900&display=swap" rel="stylesheet">
<style>
  :root {
    --bg-outer: #2a2a2a;
    --bg-inner: #474747;
    --card-dark: #3b3b3b;
    --card-light: #ffffff;
    --ink-dark: #333333;
    --ink-muted: #6b6b6b;
    --ink-light: #ffffff;
    --ink-soft: #e6e6e6;
  }
  * { box-sizing: border-box; margin: 0; padding: 0; }
  html, body { width: 1200px; height: 675px; overflow: hidden; }
  body {
    font-family: "Lato", sans-serif;
    background: radial-gradient(ellipse at 50% 40%, var(--bg-inner), var(--bg-outer) 75%);
    position: relative;
  }
  .card {
    position: absolute;
    top: 183px;
    width: 540px;
    height: 309px;
    overflow: hidden;
    box-shadow: 0 10px 30px rgba(0,0,0,.45);
  }

  /* Back side */
  .card-back { left: 40px; background: var(--card-dark); color: var(--ink-light); }
  .card-back .brand {
    position: absolute; left: 40px; top: 92px; width: 170px;
    display: flex; flex-direction: column; align-items: center; gap: 14px;
  }
  .brand-dot { width: 78px; height: 78px; border-radius: 50%; background: var(--ink-light); }
  .card-back .brand-name {
    font-weight: 700; font-size: 17px; letter-spacing: 2px; text-align: center; line-height: 1.2;
    color: var(--ink-light);
  }
  .services { position: absolute; left: 235px; top: 78px; }
  .services h2 { font-weight: 400; font-size: 21px; margin-bottom: 10px; }
  .services ul { list-style: none; }
  .services li {
    font-size: 14.5px; font-weight: 400; color: var(--ink-soft);
    display: flex; align-items: center; gap: 8px; line-height: 1.6;
  }
  .services li:nth-child(2) { padding-left: 10px; }
  .services li:nth-child(3) { padding-left: 20px; }
  .services li:nth-child(4) { padding-left: 30px; }
  .services li:nth-child(5) { padding-left: 40px; }
  .tick { width: 11px; height: 11px; flex: none; }

  /* Front side */
  .card-front { left: 620px; background: var(--card-light); color: var(--ink-dark); }
  .band {
    position: absolute; left: 0; right: 0; top: 150px; height: 142px;
    background: var(--card-dark);
  }
  .card-front .brand {
    position: absolute; left: 32px; top: 36px; display: flex; align-items: center; gap: 14px;
  }
  .card-front .brand-dot { width: 70px; height: 70px; background: var(--ink-dark); }
  .card-front .brand-name { font-weight: 700; color: var(--ink-dark); font-size: 26px; line-height: 1.05; letter-spacing: 1px; }
  .card-front .brand-name span { display: block; font-size: 17px; letter-spacing: 5px; }
  .person { position: absolute; right: 36px; top: 42px; text-align: right; }
  .person .name { font-weight: 700; font-size: 16px; letter-spacing: .5px; }
  .person .title { font-weight: 400; font-size: 13px; color: var(--ink-muted); margin-top: 2px; }
  .contact { position: absolute; left: 34px; top: 166px; color: var(--ink-light); font-size: 13.5px; line-height: 1.45; }
  .contact .address { margin-bottom: 8px; }
  .contact .row { display: flex; align-items: center; gap: 7px; }
  .contact svg { width: 12px; height: 12px; flex: none; }
  .seal {
    position: absolute; right: 44px; top: 112px; width: 112px; height: 112px;
    border-radius: 50%; background: var(--card-light);
  }
</style>
</head>
<body>

  <section class="card card-back" aria-label="Card back">
    <div class="brand">
      <div class="brand-dot"></div>
      <div class="brand-name">WOMBARRA<br>DEVICES</div>
    </div>
    <div class="services">
      <h2>Our Services:</h2>
      <ul>
        <li><svg class="tick" viewBox="0 0 12 12"><path d="M1 6.5 L4.5 10 L11 2" fill="none" stroke="#fff" stroke-width="2.2"/></svg>Applied electromagnetics</li>
        <li><svg class="tick" viewBox="0 0 12 12"><path d="M1 6.5 L4.5 10 L11 2" fill="none" stroke="#fff" stroke-width="2.2"/></svg>RF and high speed electronics</li>
        <li><svg class="tick" viewBox="0 0 12 12"><path d="M1 6.5 L4.5 10 L11 2" fill="none" stroke="#fff" stroke-width="2.2"/></svg>Signal and image processing</li>
        <li><svg class="tick" viewBox="0 0 12 12"><path d="M1 6.5 L4.5 10 L11 2" fill="none" stroke="#fff" stroke-width="2.2"/></svg>Electro-optical and laser systems</li>
        <li><svg class="tick" viewBox="0 0 12 12"><path d="M1 6.5 L4.5 10 L11 2" fill="none" stroke="#fff" stroke-width="2.2"/></svg>Concept-to-prototype design services</li>
      </ul>
    </div>
  </section>

  <section class="card card-front" aria-label="Card front">
    <div class="band"></div>
    <div class="brand">
      <div class="brand-dot"></div>
      <div class="brand-name">WOMBARRA<span>DEVICES</span></div>
    </div>
    <div class="person">
      <div class="name">DR COLIN HARTE</div>
      <div class="title">R&amp;D Engineer</div>
    </div>
    <div class="seal"></div>
    <div class="contact">
      <div class="address">PO Box XXX (to be confirmed)<br>Kelsby ACT 2917, Australia</div>
      <div class="row"><svg viewBox="0 0 12 12"><path d="M3 1 L5 3.5 L4 5 Q5 7.5 7 8 L8.5 7 L11 9 L9.5 11 Q2 10 1 2.5 Z" fill="#fff"/></svg>0427 563 710</div>
      <div class="row"><svg viewBox="0 0 12 12"><rect x="1" y="2.5" width="10" height="7" fill="#fff"/><path d="M1 2.5 L6 7 L11 2.5" fill="none" stroke="#3b3b3b" stroke-width="1"/></svg>colin@wombarradevices.com.au</div>
      <div class="row"><svg viewBox="0 0 12 12"><circle cx="6" cy="6" r="5" fill="none" stroke="#fff" stroke-width="1.2"/><ellipse cx="6" cy="6" rx="2.2" ry="5" fill="none" stroke="#fff" stroke-width="1"/><path d="M1 6 H11" stroke="#fff" stroke-width="1"/></svg>wombarradevices.com.au</div>
    </div>
  </section>

</body>
</html>
```